Brell Stone Company Business Cards

Front and Back Business Card - logo and text setup - cool design. I need workable photoshop or illustrator files so I can setup each employee card with design that is created
Updates

Hi everyone, thank you for the great entries. Please no more white and blue cards - there are so many already - black and silver only now please. thanks!

Target Market(s)

Construction Industry - Facility Managers

Industry/Entity Type

Construction

Contact Information for Business Card

I really like contemporary simplistic looks - clean neat....not opposed to seeing some black backrounds

Requirements
Must have
• Logo/website address with design on front only - www.brellstone-example.com (logo attached)
• Back:
• Name/Title/Company Address/Phone/email address
Nice to have
• Cool design
Should not have
• Nothing gimmicky like Fire or Water - since we are a Fire Protection company - it has all been done

```html
<!DOCTYPE html>
<html lang="en">
<head>
<meta charset="UTF-8">
<title>Brell Stone Company Business Cards</title>
<link rel="stylesheet" href="https://fonts.googleapis.com/css2?family=Poppins:wght@400;600;700&display=swap">
<style>
  :root {
    --page-bg: #3a3b3d;
    --card-bg: #26292d;
    --accent: #e8563a;
    --ink: #e6e6e6;
    --ink-soft: #c9c9c9;
    --mark-grey: #1c1e21;
    --mark-edge: #34373c;
  }
  * { margin: 0; padding: 0; box-sizing: border-box; }
  html, body { width: 1200px; height: 1200px; overflow: hidden; }
  body {
    background: var(--page-bg);
    font-family: "Poppins", sans-serif;
    display: flex;
    flex-direction: column;
    align-items: center;
    justify-content: center;
    gap: 56px;
  }
  .card {
    width: 900px;
    height: 514px;
    background: var(--card-bg);
    border-radius: 4px;
    position: relative;
    box-shadow: 0 14px 30px rgba(0,0,0,0.35);
  }

  /* Contact side */
  .card--contact {
    display: flex;
    align-items: center;
  }
  .brand-block {
    width: 470px;
    display: flex;
    justify-content: center;
    align-items: center;
    gap: 16px;
  }
  .brand-square {
    width: 22px;
    height: 22px;
    background: var(--accent);
  }
  .brand-name {
    font-weight: 700;
    font-size: 54px;
    color: var(--accent);
    letter-spacing: -1px;
    line-height: 1;
  }
  .divider {
    width: 3px;
    height: 300px;
    background: var(--accent);
  }
  .contact-block {
    padding-left: 44px;
    color: var(--ink);
  }
  .person-name {
    font-weight: 600;
    font-size: 26px;
    color: var(--accent);
    letter-spacing: 0.5px;
    text-transform: uppercase;
  }
  .person-title {
    font-size: 17px;
    color: var(--ink-soft);
    margin-bottom: 8px;
  }
  .address {
    font-size: 17px;
    line-height: 1.55;
    color: var(--ink-soft);
    margin-bottom: 10px;
  }
  .contact-list { list-style: none; }
  .contact-list li {
    display: flex;
    align-items: center;
    gap: 12px;
    font-size: 17px;
    line-height: 1.75;
    color: var(--ink);
  }
  .contact-list svg { width: 16px; height: 16px; fill: var(--accent); flex: none; }

  /* Brand side */
  .card--brand {
    display: flex;
    flex-direction: column;
    align-items: center;
    justify-content: center;
    gap: 70px;
  }
  .embossed-name {
    font-weight: 700;
    font-size: 96px;
    color: var(--mark-grey);
    letter-spacing: -2px;
    line-height: 1;
    text-shadow: 0 1px 0 var(--mark-edge);
  }
  .website {
    font-size: 22px;
    color: var(--ink);
    letter-spacing: 1px;
  }
  .website .website-highlight { color: var(--accent); }
</style>
</head>
<body>
  <section class="card card--contact" aria-label="Business card, contact side">
    <div class="brand-block">
      <span class="brand-square"></span>
      <span class="brand-name">Brell Stone</span>
    </div>
    <div class="divider"></div>
    <div class="contact-block">
      <p class="person-name">Dana Whitlow</p>
      <p class="person-title">Senior Consultant</p>
      <p class="address">48 Harbor Works Lane<br>Millbrook, NY 10000</p>
      <ul class="contact-list">
        <li>
          <svg viewBox="0 0 16 16" aria-hidden="true"><path d="M3 1l3 0 1 4-2 1c1 2 3 4 5 5l1-2 4 1 0 3c0 1-1 2-2 2C7 15 1 9 1 3c0-1 1-2 2-2z"/></svg>
          (555) 014-2210
        </li>
        <li>
          <svg viewBox="0 0 16 16" aria-hidden="true"><path d="M4 0h8a1 1 0 0 1 1 1v14a1 1 0 0 1-1 1H4a1 1 0 0 1-1-1V1a1 1 0 0 1 1-1zm1 2v10h6V2zm3 11a1 1 0 1 0 0 2 1 1 0 0 0 0-2z"/></svg>
          (555) 014-2211
        </li>
        <li>
          <svg viewBox="0 0 16 16" aria-hidden="true"><path d="M1 3h14v10H1zm1.5 1.2v.3L8 8.5l5.5-4v-.3zM2.5 6v5.8h11V6L8 10z"/></svg>
          info@brellstone-example.com
        </li>
        <li>
          <svg viewBox="0 0 16 16" aria-hidden="true"><path d="M8 0a8 8 0 1 0 0 16A8 8 0 0 0 8 0zm0 1.5c.9 0 1.9 1.8 2.2 5H5.8C6.1 3.3 7.1 1.5 8 1.5zm-6.4 5h2.7c.1-1.7.5-3.2 1-4.2A6.5 6.5 0 0 0 1.6 6.5zm0 3a6.5 6.5 0 0 0 3.7 4.2c-.5-1-.9-2.5-1-4.2zm4.2 0c.3 3.2 1.3 5 2.2 5s1.9-1.8 2.2-5zm5.9 0c-.1 1.7-.5 3.2-1 4.2a6.5 6.5 0 0 0 3.7-4.2zm2.7-3a6.5 6.5 0 0 0-3.7-4.2c.5 1 .9 2.5 1 4.2z"/></svg>
          www.brellstone-example.com
        </li>
      </ul>
    </div>
  </section>

  <section class="card card--brand" aria-label="Business card, brand side">
    <span class="embossed-name">Brell Stone</span>
    <p class="website">www.<span class="website-highlight">brellstone-example</span>.com</p>
  </section>
</body>
</html>
```